The best Social Research house in LatinAmerica needs a Business Card

We need a greeting card that does justice to our everyday work. Marenta Civica is a group of highly selected social academic minds (6 academicians selected among 800+ candidates) that analyses the field work done by our network of 56 social anthropologists in 7 Latin American countries. We spend months studying different social phenomena or groups of people and then translate the findings into powerful insights and strategic marketing actions for our clients (from Banks to TV networks, from top worldwide consumer product Companies to Government policy design or even new product innovation initiatives). We translate social academic knowledge into tangible actions. We already have a logo and we like it, but remain open for new and different proposals on size or form. We do something very different and we need a card as different as we are.
Target Market(s)
Top Management from Top Companies that need (and like) to be surprised!
Industry/Entity Type
Marketing
Look and feel

```html
<!DOCTYPE html>
<html lang="es">
<head>
<meta charset="utf-8">
<title>Marenta Civica — Tarjeta de presentación</title>
<link rel="stylesheet" href="https://fonts.googleapis.com/css2?family=Arvo:wght@400;700&display=swap">
<style>
  :root {
    --backdrop: #e8e4dd;
    --teal: #0c9379;
    --teal-deep: #0a7f67;
    --band: #3f6c63;
    --lime: #6cb33f;
    --paper: #ffffff;
    --ink: #333333;
    --ink-soft: #444444;
    --font-text: "Arvo", Georgia, serif;
  }
  * { box-sizing: border-box; margin: 0; padding: 0; }
  html, body {
    width: 1200px;
    height: 900px;
    overflow: hidden;
    background: var(--backdrop);
    font-family: var(--font-text);
  }
  .sheet {
    width: 1200px;
    height: 900px;
    display: flex;
    flex-direction: column;
    align-items: center;
    justify-content: center;
    gap: 40px;
  }
  .card {
    width: 700px;
    height: 400px;
    position: relative;
    box-shadow: 0 6px 18px rgba(0, 0, 0, 0.18);
  }

  /* Front */
  .card--front {
    background: var(--teal);
    display: flex;
    flex-direction: column;
    justify-content: center;
    padding-left: 120px;
  }
  .brand {
    display: flex;
    align-items: center;
    gap: 18px;
  }
  .brand__mark {
    border-radius: 50%;
    background: var(--lime);
    flex: none;
  }
  .brand__name {
    font-weight: 700;
    white-space: nowrap;
  }
  .card--front .brand__mark { width: 62px; height: 62px; }
  .card--front .brand__name { color: var(--paper); font-size: 46px; }
  .web-band {
    margin-top: 28px;
    margin-left: 80px;
    width: 400px;
    height: 42px;
    background: var(--band);
    border-left: 6px solid var(--lime);
    color: var(--paper);
    font-size: 20px;
    display: flex;
    align-items: center;
    justify-content: center;
  }

  /* Back */
  .card--back {
    background: var(--paper);
    padding: 48px 50px;
  }
  .card--back .brand__mark { width: 58px; height: 58px; background: var(--teal-deep); }
  .card--back .brand__name { color: var(--teal-deep); font-size: 44px; }
  .details {
    position: absolute;
    left: 50px;
    right: 40px;
    top: 228px;
    display: flex;
    gap: 60px;
  }
  .person { width: 250px; }
  .person__name {
    font-size: 32px;
    color: var(--ink);
    font-weight: 400;
  }
  .person__role {
    font-size: 18px;
    color: var(--ink-soft);
    margin-top: 4px;
  }
  .contact {
    list-style: none;
    display: flex;
    flex-direction: column;
    gap: 14px;
    padding-top: 14px;
  }
  .contact__item {
    display: flex;
    align-items: flex-start;
    gap: 14px;
    font-size: 19px;
    color: var(--ink);
    line-height: 1.3;
  }
  .contact__icon { flex: none; width: 26px; height: 26px; }
</style>
</head>
<body>
<main class="sheet">

  <section class="card card--front" aria-label="Frente de la tarjeta">
    <div class="brand">
      <span class="brand__mark"></span>
      <span class="brand__name">Marenta Civica</span>
    </div>
    <div class="web-band">www.marenta-civica.com</div>
  </section>

  <section class="card card--back" aria-label="Reverso de la tarjeta">
    <div class="brand">
      <span class="brand__mark"></span>
      <span class="brand__name">Marenta Civica</span>
    </div>

    <div class="details">
      <div class="person">
        <h1 class="person__name">Tomás Arvide</h1>
        <p class="person__role">Gabinete de Análisis</p>
      </div>

      <ul class="contact">
        <li class="contact__item">
          <svg class="contact__icon" viewBox="0 0 26 26" aria-hidden="true">
            <circle cx="13" cy="13" r="13" fill="#6cb33f"/>
            <path d="M9 7.5c.6-.4 1.3-.3 1.7.3l1 1.6c.3.5.2 1.1-.2 1.5l-.7.6c.6 1.4 1.6 2.5 3 3.2l.6-.7c.4-.4 1-.5 1.5-.2l1.6 1c.6.4.7 1.1.3 1.7-.8 1.2-2.1 1.6-3.4 1-3-1.3-5.2-3.6-6.3-6.6-.4-1.3 0-2.6.9-3.4z" fill="#fff"/>
          </svg>
          <span>(55) 5550 1274</span>
        </li>
        <li class="contact__item">
          <svg class="contact__icon" viewBox="0 0 26 26" aria-hidden="true">
            <circle cx="13" cy="13" r="13" fill="#6cb33f"/>
            <rect x="7" y="8.5" width="12" height="9" rx="1" fill="#fff"/>
            <path d="M7.5 9l5.5 4.5L18.5 9" fill="none" stroke="#6cb33f" stroke-width="1.2"/>
          </svg>
          <span>tomas.arvide@marenta-civica.com</span>
        </li>
        <li class="contact__item">
          <svg class="contact__icon" viewBox="0 0 26 26" aria-hidden="true">
            <circle cx="13" cy="13" r="13" fill="#6cb33f"/>
            <path d="M13 6a4.5 4.5 0 0 0-4.5 4.5c0 3.3 4.5 8.5 4.5 8.5s4.5-5.2 4.5-8.5A4.5 4.5 0 0 0 13 6z" fill="#fff"/>
            <circle cx="13" cy="10.5" r="1.7" fill="#6cb33f"/>
          </svg>
          <span>Alamedas 14. Col. Roma<br>Mexico DF 06700. MX.</span>
        </li>
      </ul>
    </div>
  </section>

</main>
</body>
</html>
```